Lanternfield Drinks business cards

We need a business card design for our new logo. The company is modern, progressive, professional, yet approachable. The key products are ready to drink bottles and cans of coffee based beverages.
These cards will be a critical part of the first impression made by our sales organization, business development team, and all external facing personnel.
Card can be a vertical or horizontal orientation.

Target Market(s)

Customers, suppliers, business partners

Industry/Entity Type

Business

Contact Information for Business Card

Business cards should feature Company Name and Logo.

Font styles to use
Serif

Colors

Designer to choose colors to be used in the design.

Requirements
Must have
• Strong readability of Name, phone #, mobile number and email address.
• Job title, website url, Street Address, and other details can be secondary level readability.
Nice to have
• High impact, simplistic quality design.
• Ok to utilize the 'H in the box' separate from the company name

```html
<!DOCTYPE html>
<html lang="en">
<head>
<meta charset="utf-8">
<title>Lanternfield Drinks – Business Cards</title>
<link rel="stylesheet" href="https://fonts.googleapis.com/css2?family=Cinzel:wght@700&family=Roboto+Slab:wght@400;600&display=swap">
<style>
  :root {
    --bg: #161616;
    --orange: #ef6a33;
    --orange-deep: #e85a2a;
    --orange-soft: #f2894d;
    --gold: #e9a43a;
    --white: #ffffff;
    --paper: #fbfbfb;
  }
  * { box-sizing: border-box; margin: 0; padding: 0; }
  html, body { width: 1200px; height: 864px; overflow: hidden; background: var(--bg); }
  .stage {
    width: 1200px; height: 864px;
    display: flex; align-items: center; justify-content: center; gap: 40px;
  }
  .card {
    position: relative; width: 520px; height: 298px; overflow: hidden;
    border-radius: 3px;
  }

  /* Front */
  .card-front {
    background: linear-gradient(120deg, var(--orange-soft) 0%, var(--orange) 45%, var(--orange-deep) 100%);
  }
  .band { position: absolute; left: -40px; width: 620px; transform: rotate(-2deg); }
  .band-a { top: 40px; height: 44px; background: rgba(255, 190, 120, 0.22); }
  .band-b { top: 150px; height: 70px; background: rgba(255, 200, 140, 0.16); }
  .band-c { top: 236px; height: 22px; background: rgba(255, 170, 110, 0.2); }
  .brand-name {
    position: absolute; left: 0; right: 0; top: 50%; transform: translateY(-50%);
    text-align: center;
    font-family: "Roboto Slab", serif; font-weight: 600; font-size: 30px;
    color: var(--white); white-space: nowrap;
  }

  /* Back */
  .card-back { background: var(--paper); }
  .ribbon {
    position: absolute; color: var(--white);
    background: linear-gradient(90deg, var(--orange), var(--orange-soft));
  }
  .ribbon-name {
    left: 0; top: 80px; width: 250px; height: 38px;
    clip-path: polygon(0 0, 92% 0, 100% 50%, 92% 100%, 0 100%);
    font-family: "Cinzel", serif; font-weight: 700; font-size: 16px;
    letter-spacing: 0.5px; line-height: 38px; padding-left: 24px;
  }
  .ribbon-title {
    left: 0; top: 126px; width: 250px; height: 32px;
    clip-path: polygon(0 0, 92% 0, 100% 50%, 92% 100%, 0 100%);
    font-family: "Roboto Slab", serif; font-size: 11px;
    line-height: 32px; padding-left: 60px;
  }
  .address {
    position: absolute; left: 24px; top: 184px;
    font-family: "Roboto Slab", serif; font-size: 10.5px; color: var(--gold);
  }
  .contact-list { position: absolute; right: 0; top: 62px; list-style: none; }
  .contact {
    position: relative; width: 240px; height: 30px; margin-bottom: 12px;
    clip-path: polygon(6% 0, 100% 0, 100% 100%, 6% 100%, 0 50%);
    display: flex; align-items: center; gap: 10px; padding-left: 26px;
    font-family: "Roboto Slab", serif; font-size: 11px;
  }
  .contact svg { width: 13px; height: 13px; flex: none; }
</style>
</head>
<body>
<main class="stage">
  <section class="card card-front" aria-label="Card front">
    <div class="band band-a"></div>
    <div class="band band-b"></div>
    <div class="band band-c"></div>
    <p class="brand-name">Lanternfield Drinks</p>
  </section>

  <section class="card card-back" aria-label="Card back">
    <div class="ribbon ribbon-name">Daniel Ashworth</div>
    <div class="ribbon ribbon-title">Managing Director</div>
    <p class="address">48 Alder Crest Ave. Millbrook, NY 12545</p>

    <ul class="contact-list">
      <li class="ribbon contact">
        <svg viewBox="0 0 16 16" fill="none" stroke="#fff" stroke-width="1.4"><rect x="1" y="1" width="14" height="14" rx="2"/><path d="M5 4c0 4 3 7 7 7l1-2-2-1-1 1c-1-.5-2-1.5-2.5-2.5l1-1-1-2z" fill="#fff" stroke="none"/></svg>
        <span>555.014.2280</span>
      </li>
      <li class="ribbon contact">
        <svg viewBox="0 0 16 16" fill="none" stroke="#fff" stroke-width="1.4"><rect x="4" y="1" width="8" height="14" rx="1.5"/><line x1="6.5" y1="12.5" x2="9.5" y2="12.5"/></svg>
        <span>555.019.3372</span>
      </li>
      <li class="ribbon contact">
        <svg viewBox="0 0 16 16" fill="none" stroke="#fff" stroke-width="1.4"><rect x="1" y="3" width="14" height="10" rx="1"/><path d="M1 4l7 5 7-5"/></svg>
        <span>dan@lanternfielddrinks.com</span>
      </li>
      <li class="ribbon contact">
        <svg viewBox="0 0 16 16" fill="none" stroke="#fff" stroke-width="1.3"><circle cx="8" cy="8" r="6.5"/><ellipse cx="8" cy="8" rx="3" ry="6.5"/><line x1="1.5" y1="8" x2="14.5" y2="8"/></svg>
        <span>www.lanternfielddrinks.com</span>
      </li>
    </ul>
  </section>
</main>
</body>
</html>
```